Personal training and nutrition business needs business card design

We need a business card that outlays our services and invites potential customers to join our team and take the first step to a healthier and more enjoyable life. We cater for any level of fitness and specialize in weight loss and conditioning, strength training, muscle gain and strength endurance. Whether you are just starting off or need some help getting to the next level of your journey we are here to get the job done.
We specialize in one on one or one on two personal training sessions and each program will be custom made to suit individual fitness goals of our clients

```html
<!DOCTYPE html>
<html lang="en">
<head>
<meta charset="utf-8">
<title>Stride &amp; Pulse — Business Card</title>
<link rel="stylesheet" href="https://fonts.googleapis.com/css2?family=Montserrat:wght@500;600;700&family=Arimo:wght@400&family=Oswald:wght@400&display=swap">
<style>
  :root {
    --backdrop: #2b2b2d;
    --card-dark: #1f1d1e;
    --card-dark-mark: #3a3839;
    --card-light: #ffffff;
    --ink: #111111;
    --purple: #8a3fb3;
    --purple-soft: #a24fb8;
    --rule: #9a9a9a;
  }
  * { box-sizing: border-box; margin: 0; padding: 0; }
  html, body {
    width: 1200px; height: 1040px; overflow: hidden;
    background: var(--backdrop);
  }
  .stage {
    position: relative; width: 1200px; height: 1040px;
    display: flex; flex-direction: column; align-items: center; justify-content: center; gap: 60px;
  }
  .card {
    position: relative; width: 700px; height: 400px;
  }
  /* back side */
  .card--back {
    background: var(--card-dark);
    border-radius: 90px 0 90px 0;
    display: flex; align-items: center; justify-content: center;
  }
  .wordmark {
    font-family: "Montserrat", sans-serif; font-weight: 700;
    text-transform: uppercase; line-height: 1; white-space: nowrap;
    display: flex; align-items: center;
  }
  .wordmark__dot { border-radius: 50%; flex: none; }
  .card--back .wordmark { color: var(--card-dark-mark); font-size: 48px; letter-spacing: 3px; gap: 16px; }
  .card--back .wordmark__dot { background: var(--card-dark-mark); width: 26px; height: 26px; }

  /* front side */
  .card--front {
    background: var(--card-light);
    border-radius: 0 90px 0 90px;
    display: flex; align-items: center;
  }
  .brand {
    width: 360px; padding: 0 30px;
    display: flex; flex-direction: column; align-items: center; gap: 14px;
  }
  .card--front .wordmark { color: var(--ink); font-size: 22px; letter-spacing: 1.5px; gap: 12px; }
  .card--front .wordmark__dot { background: var(--purple); width: 18px; height: 18px; }
  .brand__tagline {
    font-family: "Oswald", sans-serif; font-size: 12px; letter-spacing: 1.5px;
    color: var(--purple-soft); text-transform: uppercase; white-space: nowrap;
  }
  .divider { width: 1px; height: 230px; background: var(--rule); flex: none; }
  .details { padding-left: 32px; padding-right: 20px; font-family: "Arimo", sans-serif; color: var(--ink); }
  .details__name {
    font-family: "Montserrat", sans-serif; font-weight: 600; font-size: 28px;
    color: var(--purple); letter-spacing: 0.5px; text-transform: uppercase; line-height: 1;
    white-space: nowrap;
  }
  .details__role { font-size: 18px; margin-top: 6px; margin-bottom: 16px; }
  .contact { list-style: none; font-size: 18px; line-height: 1.5; }
  .contact li { display: flex; align-items: center; gap: 10px; white-space: nowrap; }
  .contact svg { width: 17px; height: 17px; flex: none; }
  .contact .accent { color: var(--purple-soft); }
  .address { font-size: 18px; line-height: 1.35; margin-top: 14px; white-space: nowrap; }
</style>
</head>
<body>
<main class="stage">
  <section class="card card--back" aria-label="Card back">
    <div class="wordmark"><span class="wordmark__dot"></span>Stride &amp; Pulse</div>
  </section>

  <section class="card card--front" aria-label="Card front">
    <div class="brand">
      <div class="wordmark"><span class="wordmark__dot"></span>Stride &amp; Pulse</div>
      <p class="brand__tagline">Personal training. Nutrition. Motivation</p>
    </div>
    <div class="divider"></div>
    <div class="details">
      <h1 class="details__name">Daniel Reyes</h1>
      <p class="details__role">Managing Director</p>
      <ul class="contact">
        <li>
          <svg viewBox="0 0 24 24" fill="none" stroke="#8a3fb3" stroke-width="2"><path d="M5 3h4l2 5-2.5 1.5a11 11 0 0 0 6 6L16 13l5 2v4a2 2 0 0 1-2 2A16 16 0 0 1 3 5a2 2 0 0 1 2-2z"/></svg>
          044-123 456 789
        </li>
        <li>
          <svg viewBox="0 0 24 24" fill="#8a3fb3"><path d="M2 5h20v14H2z"/><path d="M2 5l10 8 10-8" stroke="#fff" stroke-width="1.6" fill="none"/></svg>
          info@webname.com
        </li>
        <li>
          <svg viewBox="0 0 24 24" fill="none" stroke="#8a3fb3" stroke-width="2"><circle cx="12" cy="12" r="9"/><path d="M3 12h18M12 3c3 3 3 15 0 18M12 3c-3 3-3 15 0 18"/></svg>
          <span>www.<span class="accent">websitename</span>.com</span>
        </li>
      </ul>
      <p class="address">421, Address line goes here<br>45452, Country Name</p>
    </div>
  </section>
</main>
</body>
</html>
```